Home Security Company Business Card

Looking for a eye catching business card that is non traditional and stands out but yet still looks professional. It should include all the pertinent information such as name, title, address, telephone, e-mail, website address should definitely stand out and then finally the logo.

Target Market(s)

Residential and Commercial accounts mostly upscale accounts

Industry/Entity Type

Security

Contact Information for Business Card

Name
Title
Address
Office #
Cell #
E-mail
Website

Font styles to use
Serif
Sans Serif

Requirements
Must have
• Logo, two sided color configuration
Nice to have
• You decide
Should not have
• There really aren't any.

```html
<!DOCTYPE html>
<html lang="en">
<head>
<meta charset="utf-8">
<title>Ironvale Security – Business Card</title>
<link href="https://fonts.googleapis.com/css2?family=Source+Sans+3:ital,wght@0,400;0,600;1,400&family=Tinos&display=swap" rel="stylesheet">
<style>
  :root {
    --stage: #3b3b3b;
    --card-white: #f8f8f8;
    --brand-red: #720d00;
    --brand-gold: #d9a53a;
    --title-orange: #d98a1e;
    --ink: #3d3d3d;
    --rule: #c9c9c9;
    --on-red: #f3e6dc;
  }
  * { margin: 0; padding: 0; box-sizing: border-box; }
  html, body {
    width: 1200px; height: 750px; overflow: hidden;
    background: var(--stage);
  }
  .canvas { position: relative; width: 1200px; height: 750px; }
  .card {
    position: absolute; top: 228px; width: 461px; height: 262px; overflow: hidden;
  }
  .card--front { left: 144px; background: var(--card-white); }
  .card--back { left: 612px; background: var(--brand-red); }

  .front-swoosh { position: absolute; inset: 0; width: 461px; height: 262px; }

  .brand {
    position: absolute; left: 48px; top: 86px;
    display: flex; align-items: center; gap: 10px;
  }
  .brand__mark {
    width: 72px; height: 72px; border-radius: 50%; background: var(--brand-gold);
    flex: none;
  }
  .brand__name {
    font-family: "Tinos", serif; font-weight: 400; color: var(--brand-red);
    line-height: 1; white-space: nowrap;
  }
  .brand__name .line-main { display: block; font-size: 19px; letter-spacing: 0.2px; }
  .brand__name .line-sub { display: block; font-size: 8px; margin-top: 2px; }

  .divider {
    position: absolute; left: 257px; top: 48px; width: 1px; height: 146px; background: var(--rule);
  }
  .details {
    position: absolute; left: 276px; top: 48px;
    font-family: "Source Sans 3", sans-serif; color: var(--ink);
  }
  .details__name { font-size: 16.5px; font-weight: 600; color: var(--brand-red); line-height: 1.1; }
  .details__title { font-size: 12.5px; color: var(--title-orange); line-height: 1.3; }
  .details__address { font-size: 11px; line-height: 14px; margin-top: 8px; }
  .contact-list { list-style: none; margin-top: 6px; }
  .contact-list li {
    display: flex; align-items: center; font-size: 11px; height: 17.5px; white-space: nowrap;
  }
  .contact-list svg { width: 11px; height: 11px; margin-right: 7px; fill: var(--brand-red); flex: none; }

  .back-brand {
    position: absolute; left: 0; right: 0; top: 56px;
    display: flex; flex-direction: column; align-items: center; gap: 12px;
  }
  .back-brand .brand__mark { width: 84px; height: 84px; }
  .back-brand .brand__name { color: var(--on-red); text-align: center; }
  .back-web {
    position: absolute; left: 0; right: 0; top: 216px; text-align: center;
    font-family: "Source Sans 3", sans-serif; font-style: italic; font-size: 11.5px;
    letter-spacing: 3.4px; color: var(--on-red);
  }
</style>
</head>
<body>
<main class="canvas">
  <section class="card card--front" aria-label="Business card front">
    <svg class="front-swoosh" viewBox="0 0 461 262" aria-hidden="true">
      <path d="M0,196 C120,230 300,247 461,240 L461,244 C300,251 120,236 0,207 Z" fill="#d9a53a"/>
      <path d="M0,214 C120,243 300,256 461,249 L461,262 L0,262 Z" fill="#720d00"/>
    </svg>

    <div class="brand">
      <span class="brand__mark"></span>
      <span class="brand__name">
        <span class="line-main">IRONVALE</span>
        <span class="line-sub">SECURITY SYSTEMS INC.</span>
      </span>
    </div>

    <div class="divider"></div>

    <div class="details">
      <p class="details__name">Daniel Reyes</p>
      <p class="details__title">CEO/Founder</p>
      <p class="details__address">4120 Birchwood Court<br>Fairview, Oregon 97024</p>
      <ul class="contact-list">
        <li><svg viewBox="0 0 12 12"><path d="M2.5,0.5 L4.5,2.8 L3.4,4.2 C4.2,6 5.8,7.6 7.8,8.6 L9.2,7.5 L11.5,9.5 L10.2,11.5 C5,11 1,7 0.5,1.8 Z"/></svg>503 214 7790</li>
        <li><svg viewBox="0 0 12 12"><path d="M3,0 H9 V12 H3 Z M4,1.2 V9.5 H8 V1.2 Z" fill-rule="evenodd"/></svg>503 881 4026</li>
        <li><svg viewBox="0 0 12 12"><path d="M0,2.5 H12 V10 H0 Z M0.8,3.2 L6,7 L11.2,3.2 V3 H0.8 Z" fill-rule="evenodd"/></svg>daniel@ironvale.com</li>
        <li><svg viewBox="0 0 12 12"><circle cx="6" cy="6" r="5.8"/><path d="M3,3.5 C5,3 6,5 4.5,6.5 C5.5,8.5 4,9.5 3.5,9 Z M7.5,2 C9.5,2.5 10,5 8.5,5.5 C7.5,4.5 7,3 7.5,2 Z" fill="#f8f8f8"/></svg>www.ironvale.com</li>
      </ul>
    </div>
  </section>

  <section class="card card--back" aria-label="Business card back">
    <div class="back-brand">
      <span class="brand__mark"></span>
      <span class="brand__name">
        <span class="line-main">IRONVALE</span>
        <span class="line-sub">SECURITY SYSTEMS INC.</span>
      </span>
    </div>
    <p class="back-web">www.ironvale.com</p>
  </section>
</main>
</body>
</html>
```